Business Card Design Project

Business card based on attached logo

Todd Merrick
Todd@lorvantest.com
877-514-9073 ext. 318
Www.LorvanTest.com

Industry/Entity Type

Business

```html
<!DOCTYPE html>
<html lang="en">
<head>
<meta charset="utf-8">
<title>LorvanTest Business Card</title>
<link rel="stylesheet" href="https://fonts.googleapis.com/css2?family=Roboto:wght@400;700&family=Roboto+Condensed:wght@400;700&family=Questrial&display=swap">
<style>
  :root {
    --backdrop: #efeae4;
    --label: #2b2118;
    --card-white: #ffffff;
    --brand-red: #ed1c24;
    --card-red-top: #c8202a;
    --card-red-bottom: #a0161d;
    --ink: #111111;
    --url-grey: #3a3a3a;
    --pale-grey: #ececec;
    --panel-edge: #d6d6d6;
  }
  * { margin: 0; padding: 0; box-sizing: border-box; }
  html, body { width: 1200px; height: 788px; overflow: hidden; }
  body {
    background: var(--backdrop);
    position: relative;
    font-family: "Roboto", Arial, sans-serif;
  }
  .view-label {
    position: absolute;
    width: 526px;
    text-align: center;
    font-size: 20px;
    color: var(--label);
  }
  .card {
    position: absolute;
    width: 526px;
    height: 301px;
    border-radius: 22px;
    overflow: hidden;
    background: var(--card-white);
  }
  .card--front { left: 53px; top: 73px; }
  .card--back-plain { left: 622px; top: 73px; }
  .card--back-red {
    left: 53px; top: 444px;
    background: linear-gradient(180deg, var(--card-red-top), var(--card-red-bottom));
  }
  .card--back-panel {
    left: 622px; top: 444px;
    background: linear-gradient(180deg, #f7f7f7, var(--pale-grey));
  }
  .accent-band { position: absolute; inset: 0; }
  .brand {
    position: absolute;
    display: flex;
    align-items: center;
    gap: 10px;
    font-weight: 700;
    letter-spacing: -1px;
    color: var(--ink);
    white-space: nowrap;
  }
  .brand-mark { display: inline-block; background: var(--brand-red); }
  .card--front .brand { left: 42px; top: 42px; font-size: 46px; }
  .card--front .brand-mark { width: 22px; height: 22px; }
  .brand--centered { left: 0; right: 0; justify-content: center; font-size: 54px; }
  .brand--centered .brand-mark { width: 26px; height: 26px; }
  .card--back-plain .brand, .card--back-red .brand { top: 92px; }
  .card--back-red .brand-mark { background: var(--card-white); }
  .card--back-panel .brand { top: 118px; font-size: 40px; }
  .card--back-panel .brand-mark { width: 20px; height: 20px; }
  .holder-name {
    position: absolute;
    left: 51px; top: 188px;
    font-weight: 700;
    font-size: 17px;
    color: var(--brand-red);
  }
  .contact-list {
    position: absolute;
    right: 19px; top: 219px;
    list-style: none;
    text-align: right;
    font-family: "Roboto Condensed", Arial, sans-serif;
    font-size: 13.5px;
    line-height: 24px;
    color: var(--card-white);
  }
  .contact-list b { font-weight: 700; }
  .web-address {
    position: absolute;
    left: 0; right: 0; top: 248px;
    text-align: center;
    font-family: "Questrial", "Century Gothic", sans-serif;
    font-size: 18px;
    color: var(--url-grey);
  }
  .card--back-red .web-address { color: var(--card-white); }
  .raised-panel {
    position: absolute;
    left: 81px; top: 84px;
    width: 360px; height: 127px;
    background: #fbfbfb;
    border: 1px solid var(--panel-edge);
    border-radius: 3px;
  }
</style>
</head>
<body>

  <p class="view-label" style="left:53px; top:34px;">Front</p>
  <p class="view-label" style="left:622px; top:34px;">Back - 1</p>
  <p class="view-label" style="left:53px; top:404px;">Back - 2</p>
  <p class="view-label" style="left:622px; top:404px;">Back - 3</p>

  <section class="card card--front">
    <svg class="accent-band" width="526" height="301" viewBox="0 0 526 301" role="img" aria-label="Red wave band decoration">
      <path d="M0 240 C 110 270, 190 250, 270 200 C 350 150, 430 112, 526 104 L526 301 L0 301 Z" fill="var(--brand-red)"/>
    </svg>
    <div class="brand"><span>LorvanTest</span><span class="brand-mark"></span></div>
    <p class="holder-name">Todd Merrick</p>
    <ul class="contact-list">
      <li><b>p :</b> 877-514-9073 ext. 318</li>
      <li><b>e :</b> Todd@lorvantest.com</li>
      <li><b>w :</b> www.LorvanTest.com</li>
    </ul>
  </section>

  <section class="card card--back-plain">
    <div class="brand brand--centered"><span>LorvanTest</span><span class="brand-mark"></span></div>
    <p class="web-address">www.LorvanTest.com</p>
  </section>

  <section class="card card--back-red">
    <div class="brand brand--centered"><span>LorvanTest</span><span class="brand-mark"></span></div>
    <p class="web-address">www.LorvanTest.com</p>
  </section>

  <section class="card card--back-panel">
    <div class="raised-panel"></div>
    <div class="brand brand--centered"><span>LorvanTest</span><span class="brand-mark"></span></div>
    <p class="web-address">www.LorvanTest.com</p>
  </section>

</body>
</html>
```